Construction business card

I need a new business card, they can connect with my logo, brand.
What we do is residential house , design and build
I like: Navy blue / black
I attached our logo, brand,
and, some idea for business card.

```html
<!DOCTYPE html>
<html lang="en">
<head>
<meta charset="utf-8">
<title>Hartwell Building Group – Business Card</title>
<link href="https://fonts.googleapis.com/css2?family=Montserrat:wght@300;400&family=Oswald:wght@700&family=Roboto:wght@400;700;900&display=swap" rel="stylesheet">
<style>
  :root {
    --backdrop: #2b2d31;
    --navy: #0b1f4d;
    --navy-deep: #081638;
    --black: #050608;
    --accent: #3d8ee0;
    --white: #ffffff;
    --muted: #dfe6f2;
  }
  * { box-sizing: border-box; margin: 0; padding: 0; }
  html, body {
    width: 1200px; height: 800px; overflow: hidden;
    background: var(--backdrop);
  }
  .canvas {
    position: relative; width: 1200px; height: 800px;
  }
  .card {
    position: absolute; width: 540px; height: 310px; top: 245px;
    overflow: hidden; border-radius: 3px;
    box-shadow: 0 10px 30px rgba(0,0,0,.45);
  }
  .card--front { left: 40px; }
  .card--back  { left: 620px; }
  .card__art { position: absolute; inset: 0; width: 100%; height: 100%; }

  /* Front */
  .brand-name {
    position: absolute; left: 0; right: 0; top: 70px;
    text-align: center; color: var(--white);
    font-family: 'Roboto', sans-serif; font-weight: 900;
    font-size: 44px; line-height: 1; letter-spacing: 1px;
  }
  .brand-name--sub {
    top: 122px; font-size: 20px; letter-spacing: 4px;
  }
  .tagline {
    position: absolute; left: 0; right: 0; top: 218px;
    text-align: center; color: var(--white);
    font-family: 'Montserrat', sans-serif; font-weight: 300;
    font-size: 40px; line-height: 1;
  }
  .tagline__accent { color: var(--accent); }

  /* Back */
  .services {
    position: absolute; left: 22px; top: 112px; width: 250px;
  }
  .services__title {
    font-family: 'Oswald', sans-serif; font-weight: 700;
    font-size: 27px; color: var(--white); letter-spacing: .5px;
    margin-bottom: 10px;
  }
  .services__list { list-style: none; }
  .services__item {
    position: relative; padding-left: 24px; margin-bottom: 7px;
    font-family: 'Roboto', sans-serif; font-size: 13.5px;
    color: var(--white); line-height: 1.25;
  }
  .services__item::before {
    content: ""; position: absolute; left: 2px; top: 4px;
    width: 9px; height: 9px; background: var(--accent);
  }
  .back-brand {
    position: absolute; left: 300px; top: 62px; width: 225px;
    font-family: 'Roboto', sans-serif; font-weight: 900;
    font-size: 40px; line-height: 1; color: var(--white);
  }
  .contact {
    position: absolute; left: 300px; top: 150px; list-style: none;
  }
  .contact__row {
    display: flex; align-items: flex-start; gap: 8px;
    font-family: 'Roboto', sans-serif; font-size: 12.5px;
    color: var(--muted); margin-bottom: 9px; line-height: 1.3;
  }
  .contact__icon { flex: 0 0 16px; width: 16px; height: 16px; }
</style>
</head>
<body>
<main class="canvas">

  <section class="card card--front" aria-label="Business card front">
    <svg class="card__art" viewBox="0 0 540 310" aria-hidden="true">
      <rect width="540" height="310" fill="var(--navy)"/>
      <rect y="180" width="540" height="130" fill="var(--black)"/>
      <g stroke="var(--accent)" fill="none">
        <line x1="0" y1="180" x2="150" y2="180" stroke-width="3"/>
        <line x1="400" y1="180" x2="540" y2="180" stroke-width="3"/>
        <line x1="18" y1="20" x2="18" y2="300" stroke-width="1.2"/>
        <line x1="42" y1="165" x2="42" y2="300" stroke-width="1.2"/>
        <line x1="520" y1="10" x2="520" y2="290" stroke-width="1.2"/>
        <line x1="498" y1="40" x2="498" y2="170" stroke-width="1.2"/>
        <line x1="440" y1="85" x2="540" y2="85" stroke-width="1.2"/>
        <line x1="30" y1="285" x2="150" y2="285" stroke-width="1.2"/>
      </g>
    </svg>
    <h1 class="brand-name">HARTWELL</h1>
    <p class="brand-name brand-name--sub">BUILDING GROUP</p>
    <p class="tagline">Design <span class="tagline__accent">&amp; Build</span></p>
  </section>

  <section class="card card--back" aria-label="Business card back">
    <svg class="card__art" viewBox="0 0 540 310" aria-hidden="true">
      <defs>
        <linearGradient id="backNavy" x1="0" y1="0" x2="1" y2="1">
          <stop offset="0" stop-color="var(--navy-deep)"/>
          <stop offset="1" stop-color="var(--navy)"/>
        </linearGradient>
      </defs>
      <rect width="540" height="310" fill="url(#backNavy)"/>
      <polygon points="0,95 232,95 282,145 282,310 0,310" fill="var(--black)"/>
    </svg>

    <div class="services">
      <h2 class="services__title">OUR SERVICES</h2>
      <ul class="services__list">
        <li class="services__item">Design &amp; Planning</li>
        <li class="services__item">Residential Construction</li>
        <li class="services__item">Multi-Unit Construction</li>
        <li class="services__item">Extensions/Granny<br>Flat/Bungalow</li>
      </ul>
    </div>

    <p class="back-brand">HARTWELL</p>

    <ul class="contact">
      <li class="contact__row">
        <svg class="contact__icon" viewBox="0 0 16 16" aria-hidden="true"><circle cx="8" cy="8" r="8" fill="var(--accent)"/><path d="M5.3 4.2l1.4 1.5-.7 1c.5 1.1 1.3 1.9 2.3 2.4l1-.7 1.5 1.4-.9 1.3C7.6 10.9 5 8.4 4.2 5.1z" fill="var(--white)"/></svg>
        <span>0412 555 308</span>
      </li>
      <li class="contact__row">
        <svg class="contact__icon" viewBox="0 0 16 16" aria-hidden="true"><circle cx="8" cy="8" r="8" fill="var(--accent)"/><rect x="4" y="5.2" width="8" height="5.6" fill="none" stroke="var(--white)" stroke-width="1"/><path d="M4 5.4l4 3 4-3" fill="none" stroke="var(--white)" stroke-width="1"/></svg>
        <span>info@hartwellbuilds.com.au</span>
      </li>
      <li class="contact__row">
        <svg class="contact__icon" viewBox="0 0 16 16" aria-hidden="true"><circle cx="8" cy="8" r="8" fill="var(--accent)"/><g fill="none" stroke="var(--white)" stroke-width=".9"><circle cx="8" cy="8" r="4"/><ellipse cx="8" cy="8" rx="1.8" ry="4"/><line x1="4" y1="8" x2="12" y2="8"/></g></svg>
        <span>www.hartwellbuilds.com.au</span>
      </li>
      <li class="contact__row">
        <svg class="contact__icon" viewBox="0 0 16 16" aria-hidden="true"><circle cx="8" cy="8" r="8" fill="var(--accent)"/><path d="M8 3.5a3 3 0 0 1 3 3c0 2.2-3 6-3 6s-3-3.8-3-6a3 3 0 0 1 3-3z" fill="var(--white)"/><circle cx="8" cy="6.5" r="1.1" fill="var(--accent)"/></svg>
        <span>42 Maple Rd, Oakridge,<br>VIC 3000</span>
      </li>
    </ul>
  </section>

</main>
</body>
</html>
```